Artwork for New Single, ”Keep Still”

Unique design describing Silence.
Use the pictures provided for ideas.
Looking for something out the box, different.
Make this stand out. Modern times or futuristic.
Imagination welcomed.
BRINDLE ENTERTAINMENT INC.
Artist name is Brindle
Song Title: Keep Still

Target Market(s)

Millennials, Trap music listeners, Hardcore rap fans.

Colors

Designer to choose colors to be used in the design.

Requirements
Nice to have
• Bold, serious designs. Make a statement. Masculine, professional in nature.

```html
<!DOCTYPE html>
<html lang="en">
<head>
<meta charset="utf-8">
<title>Brindle — Keep Still</title>
<link href="https://fonts.googleapis.com/css2?family=Montserrat:wght@300;800&display=swap" rel="stylesheet">
<style>
  :root {
    --bg: #000000;
    --sky-top: #d3e2ee;
    --sky-mid: #5fb0dc;
    --ridge: #2a8fcb;
    --valley: #135fa3;
    --valley-deep: #1560a6;
    --halo: rgba(255, 255, 255, 0.42);
    --core-top: #8fa6ab;
    --core-bottom: #0d0f10;
    --lens: #9eadb0;
    --ink: #ffffff;
  }
  html, body {
    margin: 0;
    padding: 0;
    width: 1200px;
    height: 1200px;
    overflow: hidden;
    background: var(--bg);
  }
  .cover {
    position: relative;
    width: 1200px;
    height: 1200px;
    background: var(--bg);
  }
  .cover__art {
    position: absolute;
    inset: 0;
  }
  .cover__title {
    position: absolute;
    left: 0;
    right: 0;
    top: 535px;
    margin: 0;
    text-align: center;
    font-family: "Montserrat", sans-serif;
    font-weight: 800;
    font-size: 64px;
    line-height: 1;
    letter-spacing: 0.12em;
    padding-left: 0.12em;
    color: var(--ink);
  }
  .cover__rule {
    position: absolute;
    left: 418px;
    width: 364px;
    top: 609px;
    height: 2px;
    background: var(--ink);
    border: 0;
    margin: 0;
  }
  .cover__single {
    position: absolute;
    left: 0;
    right: 0;
    top: 624px;
    margin: 0;
    text-align: center;
    font-family: "Montserrat", sans-serif;
    font-weight: 300;
    font-size: 30px;
    line-height: 1;
    letter-spacing: 0.2em;
    padding-left: 0.2em;
    color: var(--ink);
  }
</style>
</head>
<body>
<main class="cover">
  <svg class="cover__art" width="1200" height="1200" viewBox="0 0 1200 1200">
    <defs>
      <linearGradient id="landscape" x1="0" y1="0" x2="0" y2="1">
        <stop offset="0" stop-color="var(--sky-top)"/>
        <stop offset="0.25" stop-color="var(--sky-mid)"/>
        <stop offset="0.55" stop-color="var(--ridge)"/>
        <stop offset="0.68" stop-color="var(--valley)"/>
        <stop offset="1" stop-color="var(--valley-deep)"/>
      </linearGradient>
      <linearGradient id="halo" x1="0" y1="0" x2="0" y2="1">
        <stop offset="0" stop-color="#ffffff" stop-opacity="0.8"/>
        <stop offset="0.45" stop-color="#ffffff" stop-opacity="0.35"/>
        <stop offset="1" stop-color="#ffffff" stop-opacity="0"/>
      </linearGradient>
      <linearGradient id="core" x1="0" y1="0" x2="0" y2="1">
        <stop offset="0" stop-color="var(--core-top)"/>
        <stop offset="0.42" stop-color="#8b9ea2"/>
        <stop offset="0.6" stop-color="#5d6668"/>
        <stop offset="1" stop-color="var(--core-bottom)"/>
      </linearGradient>
    </defs>

    <g class="landscape" role="img" aria-label="Misty blue mountain ridges fading into the sky">
      <circle class="ring-outer" cx="600" cy="600" r="495" fill="none" stroke="url(#landscape)" stroke-width="24"/>
      <circle class="disc-landscape" cx="600" cy="600" r="453" fill="url(#landscape)"/>
    </g>

    <circle class="halo" cx="600" cy="600" r="364" fill="url(#halo)"/>

    <g class="core" role="img" aria-label="Grey sky with a flock of birds rising from below">
      <circle cx="600" cy="600" r="280" fill="url(#core)"/>
      <circle class="lens" cx="600" cy="600" r="215" fill="var(--lens)"/>
    </g>
  </svg>

  <h1 class="cover__title">BRINDLE</h1>
  <hr class="cover__rule">
  <p class="cover__single">Keep Still</p>
</main>
</body>
</html>
```